To design a brand identity that is simple and creative with 'Corvane' as the brand name, I like modern simple fonts like helvetica neue, I want to print both sides of the card, I am open to dark front and white back, but the design needs to transfer well to letter heads and email signatures, I am looking for sophisticated and elegant, but open minded about clever and off the wall, I do not do 'boring' Corvane Ventures is the mother company for a small group, specialising in Management & consulting, Software development and construction, we have a high level of integrity, we are transparent and accountable for what we do. my images are provided as a guide only, Im not expecting them to be just copied, Im looking for a creator and passionate thinker, who will put life into their work.

Target Market(s)

usually business minded people who are looking for something different in me, such as leadership, confidence and focus with thinking that is per haps a little outside the box..

Industry/Entity Type

Construction

Requirements
Must have
• clean, minmalistic
Nice to have
• custom logo
Should not have
• boring, traditional

```html
<!DOCTYPE html>
<html lang="en">
<head>
<meta charset="utf-8">
<title>Corvane — Business Card</title>
<link rel="stylesheet" href="https://fonts.googleapis.com/css2?family=Open+Sans:wght@400;600;700&display=swap">
<style>
  :root {
    --bg: #e6e6ea;
    --card-dark: #231f20;
    --card-light: #ffffff;
    --brand-orange: #e2622b;
    --text-light: #ffffff;
    --text-grey: #6e6e6e;
    --band-yellow: #f7a81b;
    --band-red: #ec2a2a;
    --band-purple: #9a2d6c;
    --band-grey: #6d6a72;
    --band-teal: #19a38a;
  }
  * { box-sizing: border-box; margin: 0; padding: 0; }
  html, body {
    width: 1200px; height: 987px; overflow: hidden;
    background: var(--bg);
    font-family: "Open Sans", Helvetica, Arial, sans-serif;
  }
  .canvas { position: relative; width: 1200px; height: 987px; }

  .card {
    position: absolute; left: 220px;
    width: 760px; height: 434px;
    border-radius: 26px; overflow: hidden;
    box-shadow: 0 6px 18px rgba(0,0,0,0.12);
  }
  .card--back { top: 40px; background: var(--card-light); }
  .card--front { top: 513px; background: var(--card-dark); }

  .brand {
    position: absolute; left: 0; right: 0;
    display: flex; align-items: center; justify-content: center; gap: 22px;
  }
  .brand__dot {
    width: 40px; height: 40px; border-radius: 50%;
    background: var(--brand-orange);
  }
  .brand__name {
    font-weight: 600; color: var(--brand-orange);
    font-size: 72px; line-height: 1; letter-spacing: 12px;
    text-transform: uppercase;
  }
  .card--back .brand { top: 150px; }
  .card--front .brand { top: 62px; }

  .tagline {
    position: absolute; left: 0; right: 0; top: 260px;
    text-align: center;
    font-size: 24px; letter-spacing: 1px; color: var(--text-grey);
  }

  .band {
    position: absolute; left: 0; top: 196px; width: 100%; height: 156px;
    background: linear-gradient(90deg, var(--band-yellow) 0%, var(--band-red) 28%, var(--band-purple) 55%, var(--band-grey) 78%, var(--band-teal) 100%);
    display: flex; align-items: center;
  }
  .person { width: 300px; text-align: right; color: var(--text-light); }
  .person__name { font-weight: 700; font-size: 27px; line-height: 1.2; }
  .person__title { font-size: 21px; line-height: 1.3; }
  .divider {
    width: 2px; height: 96px; margin: 0 22px;
    background: rgba(255,255,255,0.7);
  }
  .contact { list-style: none; color: var(--text-light); font-size: 21px; line-height: 1.5; }
  .contact li { display: flex; align-items: center; gap: 8px; }
  .contact svg { width: 18px; height: 18px; fill: var(--text-light); }

  .services {
    position: absolute; left: 0; right: 0; top: 372px;
    text-align: center; color: var(--brand-orange);
    font-size: 30px; letter-spacing: 0.5px;
  }
  .services .sep { color: var(--text-light); font-size: 20px; margin: 0 8px; vertical-align: middle; }
</style>
</head>
<body>
<main class="canvas">

  <section class="card card--back" aria-label="Card back">
    <div class="brand">
      <span class="brand__dot"></span>
      <span class="brand__name">Corvane</span>
    </div>
    <p class="tagline">Leadership, built with focus.</p>
  </section>

  <section class="card card--front" aria-label="Card front">
    <div class="brand">
      <span class="brand__dot"></span>
      <span class="brand__name">Corvane</span>
    </div>

    <div class="band">
      <div class="person">
        <p class="person__name">Your Name</p>
        <p class="person__title">Title</p>
      </div>
      <span class="divider"></span>
      <ul class="contact">
        <li>
          <svg viewBox="0 0 24 24" aria-hidden="true"><path d="M6.6 10.8a15.1 15.1 0 0 0 6.6 6.6l2.2-2.2a1 1 0 0 1 1-.25 11.4 11.4 0 0 0 3.6.57 1 1 0 0 1 1 1V20a1 1 0 0 1-1 1A17 17 0 0 1 3 4a1 1 0 0 1 1-1h3.5a1 1 0 0 1 1 1c0 1.25.2 2.45.57 3.57a1 1 0 0 1-.25 1z"/></svg>
          +61 0400 555 210
        </li>
        <li>
          <svg viewBox="0 0 24 24" aria-hidden="true"><path d="M3 5h18a1 1 0 0 1 1 1v12a1 1 0 0 1-1 1H3a1 1 0 0 1-1-1V6a1 1 0 0 1 1-1zm9 7.5L4 7.3V17h16V7.3z"/></svg>
          Names@corvane.ventures
        </li>
        <li>Po Box 415 Alder 6100</li>
      </ul>
    </div>

    <p class="services">Management<span class="sep">•</span>Software<span class="sep">•</span>Construction</p>
  </section>

</main>
</body>
</html>
```